Business Card Design

Looking for business card designs for a new business. there will be two cards of the same design (both lots of information below in contact info). We would like the logo diagonally across the card with the information split above and below the logo similar to sketch. happy to look at similar alternatives
Please use same colours as in logo design

Industry/Entity Type

Business

Contact Information for Business Card

Dwight Halloran
mob - 0491 738 204
ph - 02 6148 3920
fax - 02 6148 3975
email - dwight@kestrelbeams.com.au
14 Larkmoor Road, Taminda NSW 2340

Colin Marchetti
mob - 0438 912 557
ph - 02 6148 3920
fax - 02 6148 3975
email - colin@kestrelbeams.com.au

```html
<!DOCTYPE html>
<html lang="en">
<head>
<meta charset="utf-8">
<title>Kestrel Beams – Business Cards</title>
<link rel="stylesheet" href="https://fonts.googleapis.com/css2?family=Open+Sans:wght@400;600;700&display=swap">
<style>
  :root {
    --teal: #0f7c77;
    --black: #000000;
    --white: #ffffff;
    --ink: #1a1a1a;
    --text-grey: #333333;
    --backdrop: #eceae6;
  }
  * { box-sizing: border-box; margin: 0; padding: 0; }
  html, body { width: 1145px; height: 1200px; overflow: hidden; }
  body {
    position: relative;
    background: var(--backdrop);
    font-family: "Open Sans", Arial, sans-serif;
    color: var(--ink);
  }
  .card {
    position: absolute;
    width: 943px;
    height: 538px;
    background: var(--white);
    overflow: hidden;
    box-shadow: 0 2px 10px rgba(0,0,0,0.12);
  }
  .card--front { left: 19px; top: 45px; }
  .card--back { left: 163px; top: 637px; border: 1px solid #222; }

  .sweep { position: absolute; inset: 0; width: 100%; height: 100%; }

  .brand {
    position: absolute;
    display: flex;
    align-items: center;
    gap: 18px;
  }
  .brand__square { width: 58px; height: 58px; background: var(--teal); }
  .brand__name {
    font-weight: 700;
    font-size: 76px;
    line-height: 1;
    color: var(--black);
    letter-spacing: -1px;
  }
  .card--front .brand { left: 34px; top: 74px; }
  .card--back .brand { left: 0; right: 0; top: 208px; justify-content: center; }

  .holder {
    position: absolute;
    left: 30px;
    top: 346px;
    font-weight: 700;
    font-size: 29px;
    color: var(--teal);
  }
  .address {
    position: absolute;
    left: 30px;
    top: 427px;
    font-size: 22px;
    line-height: 38px;
    color: var(--text-grey);
    font-style: normal;
  }
  .contacts {
    position: absolute;
    right: 39px;
    top: 386px;
    list-style: none;
    text-align: right;
    color: var(--white);
    font-size: 22px;
    line-height: 35px;
  }
  .contacts li { display: flex; justify-content: flex-end; align-items: center; gap: 7px; }
  .contacts svg { width: 18px; height: 18px; fill: var(--white); }

  .website {
    position: absolute;
    left: 0; right: 0;
    top: 424px;
    text-align: center;
    font-size: 28px;
    letter-spacing: 2.5px;
    color: var(--ink);
  }
  .website strong { font-weight: 600; }
</style>
</head>
<body>

<section class="card card--front">
  <svg class="sweep" viewBox="0 0 733 418" preserveAspectRatio="none" aria-hidden="true">
    <path d="M218 418 C470 340 650 200 637 0 L733 0 L733 418 Z" fill="var(--teal)"/>
    <path d="M238 418 C480 332 680 182 733 40 L733 418 Z" fill="var(--black)"/>
  </svg>

  <div class="brand">
    <span class="brand__square"></span>
    <span class="brand__name">Kestrel Beams</span>
  </div>

  <h1 class="holder">Colin Marchetti</h1>
  <address class="address">14 Larkmoor Road<br>Corrabin NSW 2472</address>

  <ul class="contacts">
    <li>
      <svg viewBox="0 0 20 20" aria-label="phone"><circle cx="10" cy="10" r="9" fill="none" stroke="#fff" stroke-width="2"/><path d="M6 5 L8.5 5 L9.5 8 L8 9 Q9 11.5 11 12 L12 10.5 L15 11.5 L15 14 Q9 15 6 5Z"/></svg>
      <span>02 6148 3920</span>
    </li>
    <li>
      <svg viewBox="0 0 20 20" aria-label="mobile"><rect x="5" y="1" width="10" height="18" rx="2"/><rect x="7" y="4" width="6" height="5" fill="#000"/><rect x="7" y="11" width="6" height="5" fill="#000"/></svg>
      <span>0438 912 557</span>
    </li>
    <li>
      <svg viewBox="0 0 20 20" aria-label="fax"><rect x="5" y="3" width="10" height="6"/><rect x="2" y="9" width="16" height="8" rx="2"/><rect x="6" y="12" width="8" height="2" fill="#000"/></svg>
      <span>02 6148 3975</span>
    </li>
    <li>
      <svg viewBox="0 0 20 20" aria-label="email"><path d="M2 8 L10 3 L18 8 L18 17 L2 17 Z"/><path d="M2 8 L10 13 L18 8" fill="none" stroke="#000" stroke-width="1.5"/></svg>
      <span>colin@kestrelbeams.com.au</span>
    </li>
  </ul>
</section>

<section class="card card--back">
  <div class="brand">
    <span class="brand__square"></span>
    <span class="brand__name">Kestrel Beams</span>
  </div>
  <p class="website">www.<strong>kestrelbeams</strong>.com.au</p>
</section>

</body>
</html>
```